Web design for small empirical brand consulting company that will sell a web-based brand tool

We need a totally new and very appealing website:
Purpose: We want to attract lots of potential customers with this website... especially, we want to sell our web-based tool valuquant®... we want to be perceived as innovative, trendy, but solid and reliable… we want customers go to the website, login at „valuquant®“ (see structure), and perceive how it works.. and the contacting us or in the near future being able to buy a login and work with the tool… so we want to a) inform (on the website or send the url to customers) and b) to „force“ potential customers getting in contact with us…
Structure (e.g.): Must Home, valuquant®, About us, Contact (incl. legal notice); we are open for more, Nice to have e.g. references/clients, press... for example, we publish a nice book in a couple of months and might want to show it somewhere on the website as well...)
Layout: We would like to have more/mainly figures - may be animated or something like that – in specific those on slides 7 and 8 as well as 6 and 9 (which would be for our web-based tool valuquant®...)... excellent, but simple and with few text…
Fonts: Eurostile; CMYK 100/23/100/19, CMYK 0/0/0/70
Logo: Would you please use the lorentavo-logo used in this file?
Social Media: we think that it might make sense to be connected to chatterbay, quipline and so on as well…
Phantasy: May be it is possible to have something between a classic marketing research and an e-commerce website... just a thought... because it is mainly about the new tool that will be assessable through a login... but customers might want to contact us or vice versa in order to check how the tool will work (btw: you do not have further info about valuquant® here... I know)… I dream of having a site where people go to and by components of our tool like at brimbo… click and buy and go for it…
It is possible to program it in php or java? Thanks.
Pages I personally like: Don’t know if that helps, but I personally like those websites just they seem so simple: http:// www.pellivarn.com/, http://www.craftelune.net/... but I am veeery open
Pages I do not like anymore: my own www.lorentavo.ch

```html
<!DOCTYPE html>
<html lang="en">
<head>
<meta charset="utf-8">
<title>lorentavo – Home</title>
<link rel="stylesheet" href="https://fonts.googleapis.com/css2?family=Open+Sans:wght@400;600;700&family=Roboto:wght@400;500;700&display=swap">
<style>
:root{
  --green:#006b2d;
  --green-dark:#005a26;
  --mint:#e1f1e6;
  --grey:#6f6f6f;
  --grey-dark:#4b4b4b;
  --text:#555;
  --caption:#6c6c6c;
  --white:#fff;
}
*{box-sizing:border-box;margin:0;padding:0}
html,body{width:1200px;height:2416px;overflow:hidden}
body{font-family:"Open Sans",Arial,sans-serif;color:var(--text);background:var(--white);position:relative}
.wrap{width:840px;margin:0 auto;position:relative}
.section-title{font-family:"Roboto",Arial,sans-serif;font-weight:400;color:var(--green);font-size:21px;text-align:center;letter-spacing:.3px}
.section-sub{font-family:"Roboto",Arial,sans-serif;text-align:center;font-size:15.5px;color:#444;margin-top:2px}
.rule{width:56px;height:3px;background:var(--green);margin:10px auto 14px}
.intro{font-size:11px;text-align:center;color:#555}

/* header */
.site-header{height:83px;background:var(--mint);border-bottom:1px solid #c9dccf}
.site-header .wrap{display:flex;align-items:center;justify-content:space-between;height:83px}
.logo{display:flex;align-items:center;gap:7px;font-family:"Roboto",Arial,sans-serif;font-size:25px;color:#555;font-weight:400}
.logo-mark{width:10px;height:10px;background:var(--green)}
.nav{display:flex;gap:26px;font-family:"Roboto",Arial,sans-serif;font-size:12.5px;text-transform:uppercase;color:#666}
.nav .active{color:var(--green);font-weight:700}

/* hero */
.hero{height:498px;position:relative;background:linear-gradient(90deg,#f1f4f5 0%,#e4e9ec 35%,#bcc6cd 60%,#dde3e6 100%)}
.hero-text{position:absolute;left:182px;top:150px;font-family:"Roboto",Arial,sans-serif;color:var(--green);font-weight:700;text-transform:uppercase}
.hero-text .big{font-size:40px;line-height:48px}
.hero-text .mid{font-size:20px;line-height:31px;font-weight:500}
.hero-arrow{position:absolute;top:239px;width:20px;height:20px;border-radius:50%;background:#555;opacity:.75;display:flex;align-items:center;justify-content:center}
.hero-arrow.left{left:24px}.hero-arrow.right{right:24px}

/* welcome */
.welcome{height:614px;padding-top:20px}
.checklist{display:grid;grid-template-columns:1fr 1fr;column-gap:26px;margin-top:28px}
.checklist ul{list-style:none}
.checklist li{display:flex;gap:9px;font-size:11px;line-height:16px;margin-bottom:14px;color:#444}
.tick{flex:0 0 13px;height:13px;background:var(--green);display:flex;align-items:center;justify-content:center;margin-top:1px}
.team-head{margin-top:40px}
.team{display:grid;grid-template-columns:repeat(4,1fr);column-gap:20px;margin-top:32px}
.member{text-align:center}
.portrait{width:138px;height:158px;margin:0 auto;background:linear-gradient(160deg,#c9a58f,#8c6f5e)}
.portrait.note{background:linear-gradient(160deg,#ecebe6,#c8c6bf)}
.member h3{font-size:14px;color:var(--green);font-weight:700;margin-top:16px}
.member p{font-size:11px;line-height:19px;color:#777;margin-top:5px}

/* offer */
.offer{height:362px;background:var(--green);padding-top:26px}
.offer .section-title,.offer .section-sub,.offer .intro{color:var(--white)}
.offer .rule{background:var(--white)}
.tiles{display:flex;justify-content:space-between;margin-top:34px}
.tile{width:248px}
.tile-photo{height:138px}
.tile-cap{height:51px;background:var(--caption);color:var(--white);font-size:14.5px;font-weight:600;padding:17px 16px;text-transform:uppercase}

/* benefits */
.benefits{height:387px;background:var(--mint);padding-top:34px}
.cards{display:flex;justify-content:space-between;margin-top:34px}
.card{width:194px;height:184px;background:var(--green);color:var(--white);text-align:center;padding:24px 14px 0}
.card h3{font-size:15px;font-weight:700;margin-top:12px}
.card p{font-size:11px;line-height:17.5px;margin-top:4px}

/* why */
.why{height:344px;padding-top:38px}
.reasons{display:flex;justify-content:space-between;margin-top:22px;padding:0 42px}
.reason{width:156px;text-align:center}
.icon-box{width:110px;height:84px;border:2px solid #9a9a9a;margin:0 auto;display:flex;align-items:center;justify-content:center}
.icon-box.active{border-color:var(--green)}
.reason h3{font-size:16px;font-weight:600;color:#555;margin-top:14px}
.reason p{font-size:11px;line-height:17px;color:#888;margin-top:6px}

/* footer */
.contact-bar{height:67px;background:var(--grey);color:var(--white)}
.contact-bar .wrap{display:flex;align-items:center;height:67px;gap:28px;font-size:12.5px;font-weight:600}
.contact-item{display:flex;align-items:center;gap:7px}
.legal{height:61px;background:var(--grey-dark);color:#bbb;font-size:11px}
.legal .wrap{display:flex;justify-content:space-between;align-items:center;height:61px}
.social{display:flex;gap:16px;font-size:11px;color:#ccc}
</style>
</head>
<body>

<header class="site-header">
  <div class="wrap">
    <div class="logo"><span class="logo-mark"></span>lorentavo</div>
    <nav class="nav">
      <span class="active">Home</span><span>lorentavo</span><span>Services</span><span>Work</span><span>Credentials</span><span>Contact</span>
    </nav>
  </div>
</header>

<section class="hero" role="img" aria-label="Two businessmen shaking hands in a bright office">
  <div class="hero-text">
    <div class="big">We</div>
    <div class="mid">Measure test and model</div>
    <div class="mid">your brand and your</div>
    <div class="big">Success</div>
  </div>
  <span class="hero-arrow left"><svg width="8" height="10" viewBox="0 0 8 10"><path d="M6 1L2 5l4 4" stroke="#fff" stroke-width="2" fill="none"/></svg></span>
  <span class="hero-arrow right"><svg width="8" height="10" viewBox="0 0 8 10"><path d="M2 1l4 4-4 4" stroke="#fff" stroke-width="2" fill="none"/></svg></span>
</section>

<section class="welcome">
  <div class="wrap">
    <h2 class="section-title">WELCOME TO LORENTAVO</h2>
    <p class="section-sub">We measure, test and model your brand and your success</p>
    <div class="rule"></div>
    <p class="intro">lorentavo ltd., a spin-off company from the University of Lindmere, specializes in empirical brand consulting:</p>
    <div class="checklist">
      <ul>
        <li><span class="tick"><svg width="9" height="8" viewBox="0 0 9 8"><path d="M1 4l2.5 2.5L8 1" stroke="#fff" stroke-width="1.6" fill="none"/></svg></span>Testing your brand using scientifically developed tools.</li>
        <li><span class="tick"><svg width="9" height="8" viewBox="0 0 9 8"><path d="M1 4l2.5 2.5L8 1" stroke="#fff" stroke-width="1.6" fill="none"/></svg></span>Detailed examination of your marketing and communication procedures.</li>
        <li><span class="tick"><svg width="9" height="8" viewBox="0 0 9 8"><path d="M1 4l2.5 2.5L8 1" stroke="#fff" stroke-width="1.6" fill="none"/></svg></span>Generating long-term effects thanks to a modeling and calculation of your brand success.</li>
      </ul>
      <ul>
        <li><span class="tick"><svg width="9" height="8" viewBox="0 0 9 8"><path d="M1 4l2.5 2.5L8 1" stroke="#fff" stroke-width="1.6" fill="none"/></svg></span>Development and implementation of strategies for your whole company, your products/services as well as for your CEO.</li>
        <li><span class="tick"><svg width="9" height="8" viewBox="0 0 9 8"><path d="M1 4l2.5 2.5L8 1" stroke="#fff" stroke-width="1.6" fill="none"/></svg></span>Cost optimization of your marketing and communication budgets by as much as 30%.</li>
      </ul>
    </div>

    <div class="team-head">
      <h2 class="section-title">OUR TEAM</h2>
      <p class="section-sub">Lorem ipsum dolor sit amet, consectetuer adipiscing</p>
    </div>
    <div class="team">
      <div class="member"><div class="portrait" role="img" aria-label="Portrait photo of Tomas Hallberg"></div><h3>Tomas Hallberg, Dr.</h3><p>Nam liber tempor cum soluta nobis eleifend option congue nihil imperd iet doming id quod mazim.</p></div>
      <div class="member"><div class="portrait" role="img" aria-label="Portrait photo of Frieder Bachwald"></div><h3>Frieder Bachwald, M.A.</h3><p>Nam liber tempor cum soluta nobis eleifend option congue nihil imperd iet doming id quod mazim.</p></div>
      <div class="member"><div class="portrait" role="img" aria-label="Portrait photo of Marten Gellert"></div><h3>Marten Gellert, Dr. des.</h3><p>Nam liber tempor cum soluta nobis eleifend option congue nihil imperd iet doming id quod mazim.</p></div>
      <div class="member"><div class="portrait note" role="img" aria-label="Handwritten note on paper"></div><h3>Kilian Kemper, M.A.*</h3><p>Nam liber tempor cum soluta nobis eleifend option congue nihil imperd iet doming id quod mazim.</p></div>
    </div>
  </div>
</section>

<section class="offer">
  <div class="wrap">
    <h2 class="section-title">LORENTAVO</h2>
    <p class="section-sub">If you can't measure it, you can't manage it</p>
    <div class="rule"></div>
    <p class="intro">Using our unique, scientifically tested instruments, lorentavo measures and models your brand, so you can effectively and successfully manage it:</p>
    <div class="tiles">
      <div class="tile"><div class="tile-photo" role="img" aria-label="Business handshake photo" style="background:linear-gradient(135deg,#9fb0c0,#e3e8ee)"></div><div class="tile-cap">Company Brand</div></div>
      <div class="tile"><div class="tile-photo" role="img" aria-label="Team reviewing charts at a desk" style="background:linear-gradient(135deg,#d5dde6,#5e7590)"></div><div class="tile-cap">Product / Service</div></div>
      <div class="tile"><div class="tile-photo" role="img" aria-label="Businessmen beside a rising bar chart" style="background:linear-gradient(135deg,#ffffff,#cfd6de)"></div><div class="tile-cap">CEO Brand</div></div>
    </div>
  </div>
</section>

<section class="benefits">
  <div class="wrap">
    <h2 class="section-title">BENEFITS</h2>
    <p class="section-sub">More successful market development and activities through sound brand analysis and trend modeling using valuquant®</p>
    <div class="rule"></div>
    <p class="intro">Sustainably increase your brand equity, and subsequently your company's success, through more effective and efficient marketing &amp; communication activities:</p>
    <div class="cards">
      <div class="card">
        <svg width="38" height="38" viewBox="0 0 38 38" fill="#fff"><rect x="4" y="4" width="6" height="5"/><rect x="13" y="4" width="21" height="5"/><rect x="4" y="12" width="6" height="5"/><rect x="13" y="12" width="21" height="5"/><rect x="4" y="20" width="6" height="5"/><rect x="13" y="20" width="21" height="5"/><rect x="4" y="28" width="6" height="5"/><rect x="13" y="28" width="21" height="5"/></svg>
        <h3>Metrics</h3><p>You receive precise data for your brand perception of your target groups.</p>
      </div>
      <div class="card">
        <svg width="38" height="38" viewBox="0 0 38 38" fill="none" stroke="#fff" stroke-width="2.5"><rect x="5" y="6" width="24" height="27"/><path d="M10 14h12M10 20h10M10 26h8"/><path d="M22 26l11-13 3 3-11 13-4 1z" fill="#fff"/></svg>
        <h3>Trend Models</h3><p>Thanks to our solid trend mod-eling, you manage your brand more actively, moreprecisely and more successfully.</p>
      </div>
      <div class="card">
        <svg width="38" height="38" viewBox="0 0 38 38" fill="none" stroke="#fff" stroke-width="2.5"><circle cx="19" cy="19" r="11"/><circle cx="19" cy="19" r="4" fill="#fff"/><path d="M19 2v8M19 28v8M2 19h8M28 19h8"/></svg>
        <h3>Precision</h3><p>You are better able to reach your customers.You can better understand the needs of your customers.</p>
      </div>
      <div class="card">
        <svg width="38" height="38" viewBox="0 0 38 38" fill="none" stroke="#fff" stroke-width="2.5"><ellipse cx="19" cy="22" rx="13" ry="10"/><path d="M13 31v4M25 31v4M16 12h6"/><circle cx="19" cy="6" r="3"/></svg>
        <h3>Cost Reduction</h3><p>By using a more precise mix of communication, you are able to optimize your marketing &amp; communication budget.</p>
      </div>
    </div>
  </div>
</section>

<section class="why">
  <div class="wrap">
    <h2 class="section-title">WHY CHOOSE US</h2>
    <p class="section-sub">Lorem ipsum dolor sit amet, consectetuer adipiscing elit</p>
    <div class="rule"></div>
    <p class="intro">valuquant® provides a means to be closer to your customers, more security, more precise communication – all of which means more success</p>
    <div class="reasons">
      <div class="reason">
        <div class="icon-box"><svg width="56" height="40" viewBox="0 0 56 40" fill="#666"><path d="M2 10l12-4 10 6 8-4 10 2 12 6-4 6-10-4-12 12-6-2-4-6-12-4z"/></svg></div>
        <h3>Closeness</h3><p>valuquant® lets you get even closer to your target groups.</p>
      </div>
      <div class="reason">
        <div class="icon-box"><svg width="48" height="44" viewBox="0 0 48 44" fill="#666"><rect x="8" y="26" width="6" height="14"/><rect x="17" y="20" width="6" height="20"/><rect x="26" y="14" width="6" height="26"/><rect x="35" y="8" width="6" height="32"/><path d="M4 42h40v2H4zM4 4h2v38H4z"/><path d="M10 20L22 10l6 4 12-12" stroke="#666" stroke-width="2" fill="none"/></svg></div>
        <h3>Security</h3><p>valuquant® lets you get even closer to your target groups.</p>
      </div>
      <div class="reason">
        <div class="icon-box active"><svg width="56" height="44" viewBox="0 0 56 44" fill="#006b2d"><circle cx="14" cy="10" r="6"/><circle cx="28" cy="8" r="6"/><circle cx="42" cy="10" r="6"/><path d="M4 30c0-8 5-12 10-12s10 4 10 12zM18 28c0-8 5-12 10-12s10 4 10 12zM32 30c0-8 5-12 10-12s10 4 10 12z"/><circle cx="21" cy="24" r="5"/><circle cx="35" cy="24" r="5"/><path d="M11 42c0-7 4-10 10-10s10 3 10 10zM25 42c0-7 4-10 10-10s10 3 10 10z"/></svg></div>
        <h3>Fit</h3><p>valuquant® lets you get even closer to your target groups.</p>
      </div>
      <div class="reason">
        <div class="icon-box"><svg width="44" height="40" viewBox="0 0 44 40" fill="none" stroke="#666" stroke-width="3.5"><rect x="4" y="8" width="28" height="28"/><path d="M11 20l8 8L40 4" stroke-width="5"/></svg></div>
        <h3>Customer loyalty</h3><p>valuquant® lets you get even closer to your target groups.</p>
      </div>
    </div>
  </div>
</section>

<footer>
  <div class="contact-bar">
    <div class="wrap">
      <span class="contact-item"><svg width="16" height="24" viewBox="0 0 16 24" fill="#fff"><path d="M8 0a8 8 0 0 1 8 8c0 6-8 16-8 16S0 14 0 8a8 8 0 0 1 8-8zm0 4a4 4 0 1 0 0 8 4 4 0 0 0 0-8z"/></svg>lorentavo ltd.Lindenweg 14 CH - 8120 Aumatt SH</span>
      <span class="contact-item"><svg width="22" height="22" viewBox="0 0 22 22" fill="#fff"><path d="M3 5c1-2 3-2 4 0l2 3-2 2c1 3 3 5 6 6l2-2 3 2c2 1 2 3 0 4-3 2-8 0-11-3S1 8 3 5z"/></svg>+41 70 555 01 28</span>
      <span class="contact-item"><svg width="26" height="22" viewBox="0 0 26 22" fill="#fff"><rect x="6" y="0" width="14" height="6"/><rect x="0" y="7" width="26" height="10" rx="2"/><rect x="6" y="14" width="14" height="8" stroke="#6f6f6f" stroke-width="1.5"/></svg>+41 40 555 02 64</span>
      <span class="contact-item"><svg width="26" height="18" viewBox="0 0 26 18" fill="none" stroke="#fff" stroke-width="2"><rect x="1" y="1" width="24" height="16"/><path d="M1 1l12 10L25 1"/></svg>t.hallberg@lorentavo.ch</span>
    </div>
  </div>
  <div class="legal">
    <div class="wrap">
      <span>Copyrights@2014 lorentavo. All Right Reserved.</span>
      <span class="social"><span>chatterbay</span><span>quipline</span><span>viddex</span><span>plusring</span><span>rss</span></span>
    </div>
  </div>
</footer>

</body>
</html>
```